Website for IT consulting Company

I need a website upgrade, the existing site content is ok, I would also like to add a testimonial page, the site should be something that is easy for us to update content. You use the content from www.kelvanbrook.com as an example. I will also post update logo and artwork. I also need a contact form with some type of validation or captcha.

I added Coded to the Project

Please omit Address maps

Target Market(s)

small business, service oriented companies. We provide IT Consulting, support and mangement

Industry/Entity Type

Information Technology

Coding

Number of Pages Required

1 page

Font styles to use
Serif
Sans Serif

Requirements
Must have
• Contain logo attached, and content from existing web site www.kelvanbrook.com.
• Also need to update content easily, and be movable to different platforms.
• There is a catch phrase
• "Let us worry about your technology…” “ so you don’t have to!”
• Should be included.
Nice to have
• Testimonial page, Project page where we can post new and past projects and pictures
Should not have
• none

```html
<!DOCTYPE html>
<html lang="en">
<head>
<meta charset="utf-8">
<title>Kelvanbrook – IT Solutions</title>
<link href="https://fonts.googleapis.com/css2?family=Lato:wght@400;700&family=Roboto:wght@300;400;500&display=swap" rel="stylesheet">
<style>
:root{
  --blue:#1b8fd6;
  --blue-bright:#2aa3e6;
  --navy:#0d4f86;
  --navy-deep:#0a3a66;
  --ink:#333;
  --grey:#666;
  --line:#2a8fd0;
  --white:#fff;
}
*{margin:0;padding:0;box-sizing:border-box}
html,body{width:1200px;height:3333px;overflow:hidden}
body{position:relative;font-family:"Roboto",Arial,sans-serif;color:var(--ink);background:var(--white)}
.abs{position:absolute}

/* header */
.site-header{position:absolute;left:0;top:0;width:1200px;height:105px;background:var(--white)}
.brand{position:absolute;left:78px;top:30px;display:flex;align-items:center;gap:12px;font-family:"Lato",sans-serif;font-weight:700;font-size:30px;color:var(--navy);letter-spacing:1px;white-space:nowrap}
.brand-mark{width:34px;height:34px;background:var(--blue)}
.main-nav{position:absolute;right:78px;top:40px;display:flex;gap:30px;font-size:16px;color:#444}
.main-nav .active{color:var(--blue)}

/* hero */
.hero{position:absolute;left:0;top:105px;width:1200px;height:585px;overflow:hidden;
  background:linear-gradient(180deg,#241a4a 0%,#3b3478 35%,#2a4b8a 65%,#1f5a93 100%)}
.hero-wave{position:absolute;left:0;top:0}
.hero-kicker{position:absolute;left:80px;top:362px;font-family:"Lato",sans-serif;font-size:20px;color:var(--white)}
.hero-title{position:absolute;left:80px;top:390px;font-family:"Lato",sans-serif;font-weight:700;font-size:33px;line-height:40px;color:var(--white);text-transform:uppercase}

/* services */
.service{position:absolute;width:340px;text-align:center}
.service-icon{position:absolute;width:164px;height:164px;border-radius:50%;background:var(--white);border:10px solid var(--blue-bright);box-shadow:0 0 0 4px #d7ecf9;display:flex;align-items:center;justify-content:center}
.service h3{font-weight:400;font-size:22px;color:var(--blue);line-height:27px;margin-bottom:10px}
.service p{font-size:14px;line-height:22px;color:var(--grey)}

/* flexible */
.flex-copy{position:absolute;left:0;top:969px;width:600px;height:458px;background:linear-gradient(135deg,#2b9fe0 0%,#1a7fc8 100%);color:var(--white);padding:50px 0 0 80px}
.flex-copy h2{font-family:"Lato",sans-serif;font-weight:400;font-size:40px;margin-bottom:22px}
.flex-copy p{font-size:16px;line-height:24px;width:470px;margin-bottom:18px}
.flex-list{list-style:none;font-size:16px}
.flex-list li{display:flex;align-items:center;gap:16px;height:42px}
.flex-list .dot{width:15px;height:15px;border-radius:50%;background:var(--white);position:relative}
.flex-list .dot::after{content:"";position:absolute;left:5px;top:4px;border-left:6px solid #1f8ad0;border-top:3.5px solid transparent;border-bottom:3.5px solid transparent}
.photo{position:absolute}

/* capabilities */
.capabilities{position:absolute;left:600px;top:1427px;width:600px;height:457px;background:linear-gradient(180deg,#0f5a95 0%,#0b4677 100%);color:var(--white)}
.cap-item{position:absolute;left:70px;display:flex;align-items:center;gap:22px;font-size:20px}
.cap-item svg{width:46px;height:46px}

/* portfolio */
.section-title{position:absolute;left:0;width:1200px;text-align:center;font-family:"Roboto",sans-serif;font-weight:400;font-size:40px;color:var(--blue)}
.section-lead{position:absolute;left:250px;width:700px;text-align:center;font-size:16px;line-height:26px;color:var(--grey)}
.portfolio-item{position:absolute;top:2071px;width:261px;height:262px;overflow:hidden}
.portfolio-item .caption{position:absolute;left:18px;bottom:12px;color:var(--white)}
.portfolio-item .caption b{display:block;font-weight:400;font-size:16px}
.portfolio-item .caption span{font-size:12px;color:var(--blue-bright)}
.portfolio-item .blurb{position:absolute;left:18px;top:95px;width:220px;font-size:13px;line-height:22px;color:var(--white)}

/* testimonials */
.testimonials{position:absolute;left:0;top:2384px;width:1200px;height:323px;background:linear-gradient(90deg,#1d2a3a 0%,#2c3e52 50%,#51677e 100%)}
.testimonials h2{position:absolute;left:0;top:52px;width:1200px;text-align:center;font-weight:400;font-size:32px;color:var(--blue-bright)}
.quote{position:absolute;left:180px;top:105px;width:840px;text-align:center;font-size:16px;line-height:26px;color:var(--white)}
.quote-mark{position:absolute;font-family:"Lato",serif;font-size:60px;color:rgba(255,255,255,.5)}
.client-name{position:absolute;left:0;top:195px;width:1200px;text-align:center;font-size:19px;color:var(--white)}
.dots{position:absolute;left:572px;top:251px;display:flex;gap:10px}
.dots i{width:6px;height:6px;border-radius:50%;background:rgba(255,255,255,.4)}
.dots i:first-child{background:var(--white)}
.avatar{position:absolute;left:552px;top:2663px;width:96px;height:96px;border-radius:50%;border:5px solid var(--white);background:linear-gradient(180deg,#9fb7c9,#3f6183)}

/* contact */
.contact-info{position:absolute;left:160px;top:2925px;font-size:15px;line-height:24px;color:#444}
.contact-info .company{font-size:21px;color:var(--blue);margin-bottom:6px}
.contact-row{position:absolute;left:160px;display:flex;align-items:center;gap:30px;font-size:15px;color:#444}
.contact-row a{color:var(--blue);font-style:italic;text-decoration:none}
.contact-form{position:absolute;left:558px;top:2929px;width:500px}
.field{display:block;width:500px;height:44px;border:2px solid var(--line);border-radius:5px;margin-bottom:8px;padding:10px 14px;font:14px "Roboto",sans-serif;color:#999;background:var(--white)}
.field.message{height:82px}
.submit{display:block;width:146px;height:52px;margin-top:14px;border:none;border-radius:3px;background:var(--blue);color:var(--white);font:500 19px "Roboto",sans-serif}

/* footer */
.site-footer{position:absolute;left:0;top:3229px;width:1200px;height:104px;background:var(--navy)}
.site-footer .brand{left:78px;top:38px;gap:10px;font-size:21px;letter-spacing:.5px;color:var(--white)}
.site-footer .brand-mark{width:26px;height:26px;background:var(--white)}
.footer-nav{position:absolute;left:324px;top:27px;display:flex;gap:14px;font-size:14px;font-weight:500;color:var(--white)}
.footer-nav .active{color:var(--blue-bright)}
.copyright{position:absolute;left:394px;top:60px;font-size:14px;color:var(--white)}
.copyright span{color:var(--blue-bright)}
.social{position:absolute;top:3256px;width:46px;height:46px;border-radius:50%;background:var(--white)}
</style>
</head>
<body>

<header class="site-header">
  <div class="brand"><span class="brand-mark"></span>KELVANBROOK</div>
  <nav class="main-nav">
    <span class="active">Home</span><span>About</span><span>Services</span><span>Projects</span><span>Testimonials</span><span>Support</span><span>Careers</span><span>Contact</span>
  </nav>
</header>

<section class="hero" role="img" aria-label="City skyline at night with illuminated skyscrapers">
  <svg class="hero-wave" width="1200" height="585" viewBox="0 0 1200 585">
    <path d="M0 360 C200 320 400 300 600 360 C800 420 1000 440 1200 420 L1200 585 L0 585 Z" fill="#1c6fb4" opacity=".55"/>
    <path d="M0 312 C250 280 420 300 620 350 C820 400 1000 380 1200 330 L1200 365 C1000 410 820 430 620 380 C420 330 250 310 0 345 Z" fill="#2aa3e6"/>
    <path d="M0 500 C300 470 600 480 1200 520 L1200 585 L0 585 Z" fill="#fff"/>
  </svg>
  <div class="hero-kicker">A full service technology company</div>
  <h1 class="hero-title">IT Solutions that<br>work for your business.</h1>
</section>

<div class="service-icon" style="left:162px;top:596px">
  <svg width="70" height="60" viewBox="0 0 70 60" fill="none" stroke="#1b6fb0" stroke-width="4"><rect x="3" y="3" width="64" height="40" rx="3"/><path d="M28 43v10M42 43v10M20 55h30"/><circle cx="28" cy="22" r="7"/><circle cx="44" cy="20" r="5"/></svg>
</div>
<div class="service-icon" style="left:507px;top:596px">
  <svg width="70" height="60" viewBox="0 0 70 60" fill="none" stroke="#1b6fb0" stroke-width="4"><rect x="3" y="3" width="64" height="40" rx="3"/><path d="M28 43v10M42 43v10M20 55h30M22 32l22-18M40 12l8 2 2 8"/></svg>
</div>
<div class="service-icon" style="left:873px;top:596px">
  <svg width="70" height="60" viewBox="0 0 70 60" fill="none" stroke="#1b6fb0" stroke-width="4"><rect x="3" y="3" width="64" height="40" rx="3"/><path d="M28 43v10M42 43v10M20 55h30M18 23h34M24 17l-6 6 6 6M46 17l6 6-6 6"/></svg>
</div>

<div class="service" style="left:74px;top:780px">
  <h3>Managed IT Solutions</h3>
  <p>Our staff will design, service, administer and maintain your IT needs. We are well versed on all major operating system, and network appliances</p>
</div>
<div class="service" style="left:430px;top:780px">
  <h3>Remote Diagnostic &amp; Support</h3>
  <p>Do you need a quick solution to a technical problem? With our live remote-assistance tool, a member of our support team can view your desktop and share control of your mouse.</p>
</div>
<div class="service" style="left:790px;top:780px">
  <h3>IT Infrastructure Design &amp; Installation</h3>
  <p>Do you have more than one site? Do you need remote access? We can design and implement LANS/WANS and VPN's.</p>
</div>

<section class="flex-copy">
  <h2>Flexible Solutions</h2>
  <p>Kelvanbrook is a technology solution provider based in Houston, Texas. Our goal is to make technology a non-issue for individuals and small to medium size businesses ranging from 5 to 150 Users.</p>
  <ul class="flex-list">
    <li><span class="dot"></span>TELECOMMUNICATIONS.</li>
    <li><span class="dot"></span>DISASTER RECOVERY.</li>
    <li><span class="dot"></span>AUDIO/VIDEO MULTIMEDIA.</li>
    <li><span class="dot"></span>WEB DESIGN.</li>
  </ul>
</section>
<div class="photo" style="left:600px;top:969px;width:600px;height:458px;background:linear-gradient(135deg,#0a2340 0%,#1d5f93 55%,#7ab8de 100%)" role="img" aria-label="Businessman in a suit touching a glowing screen"></div>

<div class="photo" style="left:0;top:1427px;width:600px;height:457px;background:radial-gradient(circle at 45% 40%,#5fb8f0 0%,#1d5e9c 35%,#081c36 80%)" role="img" aria-label="Open hand holding a glowing digital globe"></div>
<section class="capabilities">
  <div class="cap-item" style="top:46px"><svg viewBox="0 0 46 46" fill="none" stroke="#fff" stroke-width="2.5"><rect x="16" y="4" width="14" height="10"/><rect x="3" y="32" width="12" height="9"/><rect x="31" y="32" width="12" height="9"/><path d="M23 14v9M9 32v-9h28v9"/></svg>Network Administration.</div>
  <div class="cap-item" style="top:119px"><svg viewBox="0 0 46 46" fill="none" stroke="#fff" stroke-width="2.5"><rect x="4" y="6" width="38" height="26" rx="2"/><path d="M18 32v6M28 32v6M13 40h20"/></svg>Desktop Support.</div>
  <div class="cap-item" style="top:181px"><svg viewBox="0 0 46 46" fill="none" stroke="#fff" stroke-width="2.5"><rect x="10" y="4" width="30" height="22" rx="2"/><path d="M25 26v14M16 42h18M10 15H4v27"/></svg>Network Cabling</div>
  <div class="cap-item" style="top:243px"><svg viewBox="0 0 46 46" fill="none" stroke="#fff" stroke-width="2.5"><path d="M5 20a26 26 0 0 1 36 0M11 27a17 17 0 0 1 24 0M17 33a8 8 0 0 1 12 0"/><circle cx="23" cy="39" r="2.5" fill="#fff"/></svg>Wireless Networks.</div>
  <div class="cap-item" style="top:305px"><svg viewBox="0 0 46 46" fill="none" stroke="#fff" stroke-width="2.5"><path d="M23 4l16 6v12c0 10-7 17-16 20C14 39 7 32 7 22V10z"/><path d="M15 23l6 6 11-12"/></svg>Antivirus Solutions.</div>
  <div class="cap-item" style="top:367px"><svg viewBox="0 0 46 46" fill="none" stroke="#fff" stroke-width="2.5"><circle cx="23" cy="23" r="18"/><path d="M5 23h36M23 5c-8 10-8 26 0 36M23 5c8 10 8 26 0 36"/></svg>Network Security.</div>
</section>

<h2 class="section-title" style="top:1930px">PORTFOLIO</h2>
<p class="section-lead" style="top:1990px">Lorem Ipsum is simply dummy text of the printing and typesetting industry. Lorem Ipsum has been the industry's standard dummy text ever since the 1500s.</p>

<div class="portfolio-item" style="left:78px;background:linear-gradient(180deg,#6d5548,#2f2724)" role="img" aria-label="Woman working on a laptop">
  <p class="blurb">Lorem Ipsum is simply dummy text of the printing and typesetting industry. Lorem Ipsum has been the industry's standard.</p>
  <div class="caption"><b>LOREM IPSUM IS SIMPLY</b><span>www.webaddress.com</span></div>
</div>
<div class="portfolio-item" style="left:339px;background:linear-gradient(180deg,#d9dde0,#3d4145)" role="img" aria-label="Woman with glasses using a smartphone">
  <div class="caption"><b>LOREM IPSUM IS SIMPLY</b><span>www.webaddress.com</span></div>
</div>
<div class="portfolio-item" style="left:600px;background:linear-gradient(180deg,#6b5e52,#2d2824)" role="img" aria-label="Man writing notes in front of a board with pinned papers">
  <div class="caption"><b>LOREM IPSUM IS SIMPLY</b><span>www.webaddress.com</span></div>
</div>
<div class="portfolio-item" style="left:861px;background:linear-gradient(180deg,#c9d4dc,#3f4a52)" role="img" aria-label="Smiling businessman in an office">
  <div class="caption"><b>LOREM IPSUM IS SIMPLY</b><span>www.webaddress.com</span></div>
</div>

<section class="testimonials" role="img" aria-label="Dim office background with hands typing on a laptop">
  <h2>WHAT CLIENTS SAY</h2>
  <span class="quote-mark" style="left:118px;top:90px">“</span>
  <p class="quote">Lorem Ipsum is simply dummy text of the printing and typesetting industry. Lorem Ipsum has been the industry's standard dummy text ever since the 1500s, when an unknown printer took a galley of type and scrambled it to make a type specimen book.</p>
  <span class="quote-mark" style="left:1040px;top:150px">”</span>
  <div class="client-name">Paul Hendry</div>
  <div class="dots"><i></i><i></i><i></i></div>
</section>
<div class="avatar" role="img" aria-label="Client portrait"></div>

<h2 class="section-title" style="top:2785px">CONTACT US</h2>
<p class="section-lead" style="top:2840px">Lorem Ipsum is simply dummy text of the printing and typesetting industry. Lorem Ipsum has been the industry's standard dummy text ever since the 1500s.</p>

<div class="contact-info">
  <svg class="abs" style="left:-2px;top:6px" width="22" height="30" viewBox="0 0 22 30"><path d="M2 4h18l-4 5 4 5H2z" fill="#1b8fd6"/><path d="M4 2v27" stroke="#1b8fd6" stroke-width="2.5"/></svg>
  <div style="padding-left:50px">
    <div class="company">Kelvanbrook Technology Group, Inc.</div>
    1180 Marlow Ave.<br>Houston,<br>Texas 77019
  </div>
</div>
<div class="contact-row" style="top:3058px">
  <svg width="22" height="22" viewBox="0 0 24 24" fill="none" stroke="#1b8fd6" stroke-width="2"><path d="M5 3h4l2 5-3 2a12 12 0 0 0 6 6l2-3 5 2v4a2 2 0 0 1-2 2C10 21 3 14 3 5a2 2 0 0 1 2-2z"/></svg>
  (555) 410-2837
</div>
<div class="contact-row" style="top:3122px">
  <svg width="22" height="18" viewBox="0 0 24 18" fill="none" stroke="#1b8fd6" stroke-width="2"><rect x="1" y="1" width="22" height="16"/><path d="M1 1l11 9 11-9"/></svg>
  <a>info@kelvanbrook.com</a>
</div>

<form class="contact-form">
  <div class="field">Name</div>
  <div class="field">E-Mail</div>
  <div class="field message">Message</div>
  <button class="submit" type="button">SUBMIT</button>
</form>

<footer class="site-footer">
  <div class="brand"><span class="brand-mark"></span>KELVANBROOK</div>
  <nav class="footer-nav">
    <span class="active">HOME</span><span>ABOUT</span><span>SERVICES</span><span>PROJECTS</span><span>SUPPORT</span><span>CAREERS</span><span>CONTACT</span>
  </nav>
  <p class="copyright">© <span>Kelvanbrook Technology Group, Inc</span> - 2017. All Rights Reserved.</p>
</footer>
<span class="social" style="left:950px"></span>
<span class="social" style="left:1013px"></span>
<span class="social" style="left:1075px"></span>

</body>
</html>
```